Request for Business Card Design

Hi. My name is Marlene, I am looking for a new business card design for my company, Quarrow Signal Instruments, LLC. I really like the design you did for Tarsel Venture and was hoping you could do something similar using our full logo and our mark. I am also open to any raised texture design using our mark. I have attached our full logo, which would need to be somewhere on the card, as well as the mark in both outline and full form, as well as our brand colors / guide. The card does not have to be white, as long as our logo and mark appear. I actually like darker colored business cards more, but am open to all options. If you are interested in working with me, please let me know. We would also take the business card design into letterhead design if you can do that.

```html
<!DOCTYPE html>
<html lang="en">
<head>
<meta charset="utf-8">
<title>Quarrow Signal Instruments — Business Card</title>
<link rel="stylesheet" href="https://fonts.googleapis.com/css2?family=Tenor+Sans&display=swap">
<style>
  :root {
    --backdrop: #2b2b2d;
    --teal: #1a8fb0;
    --teal-deep: #0d5a72;
    --teal-light: #22a3c6;
    --card-black: #06090b;
    --ink-white: #f2f4f5;
    --ink-soft: #d6dcdf;
  }
  html, body {
    margin: 0;
    width: 1200px;
    height: 900px;
    overflow: hidden;
    background: var(--backdrop);
    font-family: "Tenor Sans", "Optima", sans-serif;
  }
  .stage { position: relative; width: 1200px; height: 900px; }
  .card {
    position: absolute;
    width: 640px;
    height: 366px;
    border-radius: 22px;
    overflow: hidden;
    box-shadow: 0 10px 28px rgba(0,0,0,0.45);
  }
  /* Back side */
  .card-back { left: 120px; top: 70px; }
  .back-texture {
    position: absolute; inset: 0;
    background: linear-gradient(115deg, var(--teal-deep) 0%, var(--teal) 40%, var(--teal-light) 55%, var(--teal) 70%, var(--teal-deep) 100%);
  }
  .back-name {
    position: absolute; right: 56px; top: 150px;
    color: var(--ink-white); font-size: 15px; letter-spacing: 2px;
  }
  /* Front side */
  .card-front { left: 440px; top: 470px; background: var(--card-black); }
  .brand {
    position: absolute; left: 30px; top: 44px;
    display: flex; align-items: center; gap: 16px;
  }
  .brand-dot { width: 58px; height: 58px; border-radius: 50%; background: var(--teal); }
  .brand-name { color: var(--ink-soft); line-height: 1; }
  .brand-name .primary { display: block; font-size: 46px; letter-spacing: 5px; }
  .brand-name .secondary { display: block; font-size: 12.5px; letter-spacing: 1.4px; margin-top: 6px; }
  .divider {
    position: absolute; left: 262px; right: 26px; top: 216px;
    height: 1px; background: var(--teal);
  }
  .person { position: absolute; left: 40px; top: 196px; }
  .person-name { color: var(--ink-white); font-size: 17px; letter-spacing: 0.6px; margin: 0; }
  .person-role { color: var(--teal); font-size: 15px; letter-spacing: 0.6px; margin: 2px 0 0; }
  .contacts { list-style: none; margin: 14px 0 0; padding: 0; }
  .contacts li {
    display: flex; align-items: center; gap: 10px;
    color: var(--ink-white); font-size: 13.5px; margin-bottom: 4px;
  }
  .contacts svg { width: 14px; height: 14px; fill: none; stroke: var(--teal); stroke-width: 1.6; }
  .address {
    position: absolute; right: 34px; top: 236px;
    text-align: right; color: var(--ink-white); font-size: 13.5px; line-height: 1.55;
  }
</style>
</head>
<body>
<main class="stage">
  <section class="card card-back" aria-label="Card back">
    <div class="back-texture" role="img" aria-label="Raised repeating brand-mark texture on teal"></div>
    <span class="back-name">QUARROW</span>
  </section>

  <section class="card card-front" aria-label="Card front">
    <div class="brand">
      <span class="brand-dot"></span>
      <div class="brand-name">
        <span class="primary">QUARROW</span>
        <span class="secondary">SIGNAL INSTRUMENTS</span>
      </div>
    </div>

    <div class="divider"></div>

    <div class="person">
      <p class="person-name">DR. ELIAS VANDERMEER</p>
      <p class="person-role">PRESIDENT &amp; CEO</p>
      <ul class="contacts">
        <li><svg viewBox="0 0 16 16"><path d="M4 2l3 3-2 2a9 9 0 0 0 4 4l2-2 3 3-2 2C7 14 2 9 2 4z"/></svg>+001 555 210 4830</li>
        <li><svg viewBox="0 0 16 16"><rect x="3" y="2" width="10" height="4"/><rect x="2" y="6" width="12" height="6"/><rect x="4" y="10" width="8" height="4"/></svg>+001 555 210 4831</li>
        <li><svg viewBox="0 0 16 16"><rect x="2" y="4" width="12" height="9"/><path d="M2 4l6 5 6-5"/></svg>info@quarrowsignal.com</li>
        <li><svg viewBox="0 0 16 16"><circle cx="8" cy="8" r="6"/><ellipse cx="8" cy="8" rx="2.6" ry="6"/><path d="M2 8h12"/></svg>www.quarrowsignal.com</li>
      </ul>
    </div>

    <address class="address" style="font-style:normal">
      1180 Meridian Park Road<br>
      Fenwick, CO 80999
    </address>
  </section>
</main>
</body>
</html>
```